Fitness Equipment Repair Business Needs a Catchy New Business Card

We have an existing business card, however, it is quite plain and boring. We are expanding primarily in the commercial area (gyms, studios, apartment complexes etc). The business card will serve as eye candy to those managers/owners that can't be met for a face to face.
Originally I was planning for a brochure as well, but all of our information is better summarized on our website. (brightloopservice.ca).
I would like the card to match the colour scheme of the website and utilize the logo. It should have a professional clean feel to it, however, a little colouring outside the lines wouldn't hurt.
The example card is for my service technician (Colin Marsh). If possible I would like to be able to edit the text to use for more than one person.

Industry/Entity Type

Appliance Repair

Contact Information for Business Card

Clean, crisp and professional but needs to be eye catching. Preferably using the black, white and red colour scheme matching the website. Double sided would be nice, but is not necessary.

Colors
ec1f27
ffffff
000000

Requirements
Must have
• Must be able to edit name, phone number and title to use for multiple people. Must show the company website (brightloopservice.ca).

```html
<!DOCTYPE html>
<html lang="en">
<head>
<meta charset="utf-8">
<title>Bright Loop Service – Business Card</title>
<link rel="stylesheet" href="https://fonts.googleapis.com/css2?family=Cinzel:wght@400;700&family=PT+Sans:ital,wght@0,400;1,400&display=swap">
<style>
  :root {
    --red: #ec1f27;
    --white: #ffffff;
    --black: #000000;
    --backdrop: #e9e6e2;
    --card-shadow: rgba(0, 0, 0, 0.35);
  }
  * { box-sizing: border-box; margin: 0; padding: 0; }
  html, body {
    width: 1200px;
    height: 987px;
    overflow: hidden;
    background: var(--backdrop);
  }
  .sheet {
    position: relative;
    width: 1200px;
    height: 987px;
  }
  .card {
    position: absolute;
    left: 293px;
    width: 615px;
    height: 350px;
    background: var(--black);
    color: var(--white);
    box-shadow: 0 2px 8px var(--card-shadow);
    font-family: "PT Sans", sans-serif;
  }
  .card--front { top: 130px; }
  .card--back { top: 506px; }

  /* front */
  .brand {
    position: absolute;
    right: 37px;
    top: 80px;
    display: flex;
    align-items: center;
    gap: 10px;
  }
  .brand__mark {
    width: 12px;
    height: 12px;
    background: var(--red);
  }
  .brand__name {
    font-family: "Cinzel", serif;
    font-weight: 700;
    font-size: 16px;
    letter-spacing: 1.5px;
    color: var(--white);
  }
  .person {
    position: absolute;
    left: 36px;
    top: 173px;
  }
  .person__name {
    font-family: "Cinzel", serif;
    font-weight: 700;
    font-size: 23px;
    letter-spacing: 1.5px;
    color: var(--red);
    line-height: 1;
  }
  .person__title {
    font-family: "Cinzel", serif;
    font-weight: 400;
    font-size: 16px;
    letter-spacing: 1px;
    margin-top: 6px;
  }
  .divider {
    position: absolute;
    left: 36px;
    right: 33px;
    top: 240px;
    height: 2px;
    background: var(--white);
  }
  .contact {
    position: absolute;
    left: 36px;
    top: 254px;
    list-style: none;
    font-size: 16px;
    line-height: 23px;
  }
  .contact li {
    display: flex;
    align-items: center;
    gap: 7px;
  }
  .contact svg { width: 13px; height: 13px; fill: var(--red); }
  .address {
    position: absolute;
    right: 33px;
    top: 254px;
    text-align: right;
    font-style: normal;
    font-size: 16px;
    line-height: 23px;
  }
  .address__web { color: var(--red); }

  /* back */
  .back-brand {
    position: absolute;
    left: 0;
    right: 0;
    top: 150px;
    display: flex;
    justify-content: center;
    align-items: center;
    gap: 12px;
  }
  .back-brand__mark {
    width: 18px;
    height: 18px;
    border-radius: 50%;
    background: var(--red);
  }
  .back-brand__name {
    font-family: "Cinzel", serif;
    font-weight: 700;
    font-size: 28px;
    letter-spacing: 2px;
    color: var(--white);
  }
  .back-web {
    position: absolute;
    left: 0;
    right: 0;
    top: 280px;
    text-align: center;
    font-style: italic;
    font-size: 17px;
    letter-spacing: 1.5px;
  }
</style>
</head>
<body>
<main class="sheet">
  <section class="card card--front">
    <div class="brand">
      <span class="brand__mark"></span>
      <span class="brand__name">Bright Loop Service</span>
    </div>
    <div class="person">
      <p class="person__name">Colin Marsh</p>
      <p class="person__title">Service technician</p>
    </div>
    <div class="divider"></div>
    <ul class="contact">
      <li><svg viewBox="0 0 24 24"><path d="M6.6 10.8a15.1 15.1 0 0 0 6.6 6.6l2.2-2.2a1 1 0 0 1 1-.25 11.4 11.4 0 0 0 3.6.57 1 1 0 0 1 1 1V20a1 1 0 0 1-1 1A17 17 0 0 1 3 4a1 1 0 0 1 1-1h3.5a1 1 0 0 1 1 1c0 1.25.2 2.45.57 3.57a1 1 0 0 1-.25 1z"/></svg>587-555-0142</li>
      <li><svg viewBox="0 0 24 24"><path d="M6.6 10.8a15.1 15.1 0 0 0 6.6 6.6l2.2-2.2a1 1 0 0 1 1-.25 11.4 11.4 0 0 0 3.6.57 1 1 0 0 1 1 1V20a1 1 0 0 1-1 1A17 17 0 0 1 3 4a1 1 0 0 1 1-1h3.5a1 1 0 0 1 1 1c0 1.25.2 2.45.57 3.57a1 1 0 0 1-.25 1z"/></svg>780-555-0187</li>
      <li><svg viewBox="0 0 24 24"><path d="M2 6v12h20V6l-10 7z"/><path d="M2 5h20l-10 7z"/></svg>service@brightloopservice.ca</li>
    </ul>
    <address class="address">
      1875 Corbel Way NW<br>
      Edmonton AB T6X 4K2<br>
      <span class="address__web">www.brightloopservice.ca</span>
    </address>
  </section>

  <section class="card card--back">
    <div class="back-brand">
      <span class="back-brand__mark"></span>
      <span class="back-brand__name">Bright Loop Service</span>
    </div>
    <p class="back-web">www.brightloopservice.ca</p>
  </section>
</main>
</body>
</html>
```